creating a certificate for our flagship course

Hi,
We need a new certificate for our flagship course called Silver Harbour. We have been running this course for 25 years this year and want to get something special that represents that. We need our logos incorporated and we love to have a compass or Koru incorporated in the certificate. We like something different from your standard certificate, but not too crazy.

The text should say something along the lines of:
This certificate is awarded to ....
For successfully completing and contributing to the three day Silver Harbour programme.

signed:... date:...

to learn a bit more about this course and our company, please check our website. www.mellorquaid.co.nz

Thank you!

Target Market(s)

attendees who completed our 3 day programme.

Requirements
Must have
• Both our SH logo and our brand logo. a compass or a koru.
• a 25th year existence something on it.

```html
<!DOCTYPE html>
<html lang="en">
<head>
<meta charset="utf-8">
<title>Silver Harbour Certificate</title>
<link rel="stylesheet" href="https://fonts.googleapis.com/css2?family=Pinyon+Script&family=Cinzel:wght@700;900&family=Lato:wght@400&display=swap">
<style>
  :root {
    --green: #8cc63f;
    --green-light: #a6d45a;
    --navy: #2b2a4c;
    --ink: #2d2c3e;
    --paper: #ffffff;
    --rule: #b9b9c2;
  }
  * { margin: 0; padding: 0; box-sizing: border-box; }
  html, body { width: 848px; height: 1200px; overflow: hidden; background: var(--paper); }
  .certificate {
    position: relative;
    width: 848px;
    height: 1200px;
    background: var(--paper);
    color: var(--ink);
    font-family: "Lato", sans-serif;
    overflow: hidden;
  }
  .certificate__frame { position: absolute; inset: 0; }
  .brand-tab {
    position: absolute;
    left: 339px; top: 0;
    width: 170px; height: 236px;
    background: var(--navy);
    border-radius: 0 0 24px 24px;
    display: flex; flex-direction: column; align-items: center;
    padding-top: 46px;
  }
  .brand-tab__square {
    width: 58px; height: 58px;
    background: var(--green);
  }
  .brand-tab__name {
    margin-top: 14px;
    font-family: "Cinzel", serif;
    font-weight: 700;
    font-size: 17px;
    line-height: 1.15;
    color: var(--paper);
    text-align: left;
    letter-spacing: 0.5px;
  }
  .programme-tab {
    position: absolute;
    left: 339px; top: 224px;
    width: 170px; height: 76px;
    background: var(--green);
    border-radius: 0 0 20px 20px;
    display: flex; align-items: center; justify-content: center; gap: 10px;
  }
  .programme-tab__dot {
    width: 40px; height: 40px; border-radius: 50%;
    border: 3px solid var(--paper);
  }
  .programme-tab__name {
    font-family: "Lato", sans-serif;
    font-size: 15px;
    color: var(--paper);
  }
  .certificate__title {
    position: absolute;
    left: 0; right: 0; top: 318px;
    text-align: center;
    font-family: "Pinyon Script", cursive;
    font-size: 168px;
    line-height: 1;
    color: var(--ink);
  }
  .certificate__awarded {
    position: absolute;
    left: 0; right: 0; top: 558px;
    text-align: center;
    font-family: "Cinzel", serif;
    font-weight: 700;
    font-size: 27px;
    letter-spacing: 1px;
    color: var(--ink);
  }
  .certificate__recipient {
    position: absolute;
    left: 0; right: 0; top: 614px;
    text-align: center;
    font-family: "Pinyon Script", cursive;
    font-size: 82px;
    line-height: 1.1;
    color: var(--ink);
  }
  .certificate__recipient-rule {
    position: absolute;
    left: 214px; top: 718px;
    width: 420px; height: 2px;
    background: linear-gradient(90deg, transparent, var(--ink) 20%, var(--ink) 80%, transparent);
  }
  .certificate__reason {
    position: absolute;
    left: 60px; right: 60px; top: 770px;
    text-align: center;
    font-family: "Cinzel", serif;
    font-weight: 900;
    font-size: 34px;
    line-height: 1.32;
    letter-spacing: 2px;
    color: var(--ink);
  }
  .certificate__divider {
    position: absolute;
    left: 254px; top: 1004px;
    width: 340px; height: 2px;
    background: var(--rule);
  }
  .certificate__date {
    position: absolute;
    left: 64px; top: 1072px;
    font-size: 15px;
    line-height: 1.4;
    color: var(--ink);
  }
  .certificate__signature {
    position: absolute;
    left: 626px; top: 1072px;
    width: 160px;
    font-size: 15px;
    color: var(--ink);
    text-align: center;
  }
  .certificate__signature-line {
    margin-top: 38px;
    height: 1px;
    background: var(--rule);
  }
  .anniversary-badge {
    position: absolute;
    left: 336px; top: 1020px;
    width: 176px; height: 176px;
    border-radius: 50%;
    background: var(--green);
    display: flex; flex-direction: column; align-items: center; justify-content: center;
    color: var(--ink);
  }
  .anniversary-badge__number {
    font-family: "Cinzel", serif;
    font-weight: 900;
    font-size: 72px;
    line-height: 0.9;
  }
  .anniversary-badge__label {
    font-family: "Pinyon Script", cursive;
    font-size: 30px;
    line-height: 1;
  }
</style>
</head>
<body>
<main class="certificate">
  <svg class="certificate__frame" width="848" height="1200" viewBox="0 0 848 1200" aria-hidden="true">
    <path d="M0 0 H848 V240 C760 270 640 330 424 330 C210 330 90 270 0 240 Z" fill="var(--green)"/>
    <path d="M0 262 C100 300 220 346 424 346 C628 346 748 300 848 262" fill="none" stroke="var(--green-light)" stroke-width="4"/>
    <path d="M0 1200 V1150 C150 1120 300 1150 424 1150 C548 1150 698 1120 848 1150 V1200 Z" fill="var(--green)"/>
    <path d="M0 1138 C150 1108 300 1138 424 1138 C548 1138 698 1108 848 1138" fill="none" stroke="var(--green-light)" stroke-width="3"/>
  </svg>

  <header class="brand-tab">
    <div class="brand-tab__square"></div>
    <p class="brand-tab__name">MELLOR QUAID<br>&amp; ASSOCIATES</p>
  </header>
  <div class="programme-tab">
    <span class="programme-tab__dot"></span>
    <span class="programme-tab__name">Silver Harbour</span>
  </div>

  <h1 class="certificate__title">Certificate</h1>
  <p class="certificate__awarded">THIS CERTIFICATE IS AWARDED TO</p>
  <p class="certificate__recipient">Daniel Hughes</p>
  <div class="certificate__recipient-rule"></div>
  <p class="certificate__reason">FOR SUCCESSFULLY COMPLETING<br>AND CONTRIBUTING TO THE<br>THREE DAY SILVER HARBOUR<br>PROGRAMME</p>
  <div class="certificate__divider"></div>

  <p class="certificate__date">Lakeford,<br>30.4.2016.</p>
  <div class="certificate__signature">
    Chairman
    <div class="certificate__signature-line"></div>
  </div>

  <div class="anniversary-badge">
    <span class="anniversary-badge__number">25</span>
    <span class="anniversary-badge__label">years</span>
  </div>
</main>
</body>
</html>
```